Music Marketing Agency in need of a fully responsive website

Need a website for our music marketing agency with a nice Rev slider has the ability to take payments has a section with our work and client able to see case studies able to download our media kit in PDF can take appointments has social media and a careers upload section. Also want a prominent contact form. Nice and icons for music industry. I want them to be able to download a free Picsandra marketing download Very clean and not large icons or menu at the top very minimal menu bar this will have to go with our logo as well which I will add to order. I want this to be a membership oriented site. so there will be packages displayed or a membership form which they can use to sign up and need a login window. Also need to be able to put Tunevox playlist on the website. Save a section for past clients logos.Again this has to be a clean concept I would like pictures of Quellos such as an app promotion. Definitely want lots of flash words in bold letters across the pages when they scroll through new sections.
Updates

Need extra days to review

Target Market(s)

Urban Music

Coding

Coded - Design and coding required

Font styles to use
Serif

Colors

Designer to choose colors to be used in the design.

Requirements
Must have
• Please Add Logos attached at the Footer

```html
<!DOCTYPE html>
<html lang="en">
<head>
<meta charset="utf-8">
<title>Velvet Psalm Media – Login</title>
<link rel="stylesheet" href="https://fonts.googleapis.com/css2?family=Nunito+Sans:wght@800;900&family=Open+Sans:wght@400;600;700&display=swap">
<style>
  :root {
    --ink-white: #ffffff;
    --panel-bg: rgba(38, 22, 24, 0.78);
    --field-bg: #ffffff;
    --field-text: #3a3a3a;
    --icon-grey: #444444;
    --accent-orange: #e55a0f;
    --scene-deep: #1c2244;
    --scene-violet: #5b3657;
    --scene-rose: #b8555a;
    --scene-amber: #e2733f;
    --scene-ember: #6a2d14;
  }
  * { box-sizing: border-box; margin: 0; padding: 0; }
  html, body {
    width: 1200px;
    height: 666px;
    overflow: hidden;
    background: #111;
  }
  .login-page {
    position: relative;
    width: 1200px;
    height: 666px;
    overflow: hidden;
    font-family: "Open Sans", Arial, sans-serif;
    color: var(--ink-white);
  }
  .stage-backdrop {
    position: absolute;
    inset: 0;
    background:
      radial-gradient(ellipse 420px 300px at 1080px 90px, rgba(236,128,80,0.85), transparent 70%),
      radial-gradient(ellipse 380px 320px at 980px 420px, rgba(170,60,40,0.7), transparent 70%),
      radial-gradient(ellipse 360px 260px at 420px 180px, rgba(150,80,110,0.55), transparent 70%),
      linear-gradient(180deg, rgba(0,0,0,0) 60%, rgba(60,25,15,0.55) 100%),
      linear-gradient(90deg, var(--scene-deep) 0%, var(--scene-violet) 35%, var(--scene-rose) 65%, var(--scene-amber) 88%, var(--scene-ember) 100%);
  }
  .brand-name {
    position: absolute;
    top: 101px;
    left: 0;
    width: 100%;
    text-align: center;
    font-family: "Nunito Sans", Arial, sans-serif;
    font-weight: 900;
    font-size: 42px;
    letter-spacing: 0.5px;
    line-height: 1.2;
  }
  .login-panel {
    position: absolute;
    left: 395px;
    top: 212px;
    width: 411px;
    height: 281px;
    background: var(--panel-bg);
  }
  .login-title {
    position: absolute;
    top: 14px;
    width: 100%;
    text-align: center;
    font-family: "Nunito Sans", Arial, sans-serif;
    font-weight: 900;
    font-size: 33px;
    line-height: 1.2;
  }
  .signup-prompt {
    position: absolute;
    top: 65px;
    width: 100%;
    text-align: center;
    font-size: 19px;
    line-height: 1.3;
  }
  .field {
    position: absolute;
    left: 29px;
    width: 353px;
    height: 45px;
    background: var(--field-bg);
    display: flex;
    align-items: center;
    padding-left: 17px;
    gap: 6px;
    color: var(--field-text);
    font-size: 14px;
  }
  .field-user { top: 112px; }
  .field-password { top: 173px; }
  .field svg { width: 12px; height: 13px; fill: var(--icon-grey); flex: none; }
  .login-button {
    position: absolute;
    left: 532px;
    top: 465px;
    width: 137px;
    height: 59px;
    border-radius: 30px;
    background: var(--accent-orange);
    display: flex;
    align-items: center;
    justify-content: center;
    font-weight: 700;
    font-size: 21px;
    letter-spacing: 0.5px;
  }
  .footer-note {
    position: absolute;
    top: 612px;
    width: 100%;
    text-align: center;
    font-size: 12.5px;
  }
</style>
</head>
<body>
<main class="login-page">
  <div class="stage-backdrop" role="img" aria-label="Photo of a band performing on a warmly lit concert stage with a bass guitarist and drum kit"></div>

  <h1 class="brand-name">VELVET PSALM MEDIA</h1>

  <section class="login-panel">
    <h2 class="login-title">LOGIN</h2>
    <p class="signup-prompt">New user? Create an account</p>

    <div class="field field-user">
      <svg viewBox="0 0 12 13" aria-hidden="true"><circle cx="6" cy="3.4" r="3.2"/><path d="M0 13c0-4 2.4-5.8 6-5.8s6 1.8 6 5.8z"/></svg>
      <span>| User Name</span>
    </div>
    <div class="field field-password">
      <svg viewBox="0 0 12 13" aria-hidden="true"><path d="M3 6V4a3 3 0 0 1 6 0v2h-1.6V4a1.4 1.4 0 0 0-2.8 0v2z"/><rect x="1" y="6" width="10" height="7" rx="1"/></svg>
      <span>| Password</span>
    </div>
  </section>

  <div class="login-button">LOGIN</div>

  <footer class="footer-note">Copyrights © 2018, Velvet Psalm Media.. All rights reserved.</footer>
</main>
</body>
</html>
```